Harbor Seal Works Spray Foam Appications website

We need a custom website for our company, www.harborsealworks.example. We need something we can modify by adding/changing content, photos, updated projects, etc. We are a commercial contractor specializing in Spray Foam applications. We want the website to be very creative and easy to navigate. The main points of the website are to showcase our projects, and describe our scope of services. We provide spray foam applications to the residential and commercial market. We offer Spray Foam roofing applications, as well as Spray Foam interior insulation applications. We also provide Roof Restoration Coating Systems to refurbish old and failing metal roofs. We would be ok with a one page web design if we can get the scope of our services to flow in a single page. The designer can decide if single or multiple pages works best for our business. One of the suppliers we work with is www.verdansupply.example.

Target Market(s)

Residential Home Builders, General Contractors, Commercial Construction Companies, Property Management Groups.

Industry/Entity Type

Insulation

Number of Pages Required

5+ page

Font styles to use
Serif
Sans Serif

Colors

Designer to choose colors to be used in the design.

Requirements
Must have
• We already have a Wix page, so website must be a Wix theme design. Nice easy to navigate format. Color matched to our current logo theme. We already have brochures and would like for it to match what's already in the hands of some of our customers. Need to be able to manage content to update photos, projects, scope of service, etc., via Wix. Current hold/splash page is hosted at www.harborsealworks.example. We would also like to have this video posted on the home page: https://www.videohost.example/watch?v=QxT4pLm9ZrA&feature=share
Nice to have
• I have attached some splash videos, being able to incorporate these somehow without being overpowering would be nice.

```html
<!DOCTYPE html>
<html lang="en">
<head>
<meta charset="utf-8">
<title>Harbor Seal Works – Spray Foam Applications</title>
<link href="https://fonts.googleapis.com/css2?family=Roboto:wght@400;500;700;900&display=swap" rel="stylesheet">
<style>
:root{
  --orange:#f0a81c;
  --orange-dark:#e39c10;
  --ink:#1e1e1e;
  --dark:#232323;
  --text:#444;
  --muted:#666;
  --line:#e4e4e4;
  --white:#fff;
}
*{box-sizing:border-box;margin:0;padding:0}
html,body{width:1200px;height:5034px;overflow:hidden}
body{position:relative;font-family:'Roboto',Arial,sans-serif;color:var(--text);background:var(--white)}
.abs{position:absolute}
.btn{position:absolute;display:flex;align-items:center;justify-content:center;font-weight:700;font-size:14px;letter-spacing:.2px;text-transform:uppercase;border-radius:3px}
.btn-orange{background:var(--orange);color:var(--white)}
.btn-dark{background:var(--ink);color:var(--white)}

/* header */
.site-header{position:absolute;left:0;top:0;width:1200px;height:86px;z-index:3}
.brand{position:absolute;left:39px;top:20px;display:flex;align-items:center;gap:12px}
.brand-mark{width:46px;height:46px;border:3px solid var(--orange);border-radius:50%}
.brand-name{color:var(--orange);font-weight:700;font-size:19px;letter-spacing:.3px;text-transform:uppercase}
.main-nav{position:absolute;left:402px;top:34px;display:flex;gap:33px;font-size:14px;font-weight:700;color:var(--white)}
.main-nav .active{color:var(--orange)}
.header-cta{position:absolute;right:0;top:0;width:215px;height:86px;background:var(--orange);color:var(--white);font-weight:700;font-size:22px;display:flex;align-items:center;justify-content:center}

/* hero */
.hero{position:absolute;left:0;top:0;width:1200px;height:723px;background:linear-gradient(180deg,#3d3f40 0%,#6f7274 35%,#8a8d8f 65%,#5d6062 100%)}
.hero-title{position:absolute;left:0;top:310px;width:1200px;text-align:center;color:var(--white);font-weight:700;font-size:58px;line-height:72px;text-transform:uppercase}
.hero-phone{left:390px;top:480px;width:148px;height:46px}
.hero-quote{left:574px;top:480px;width:234px;height:46px}
.hero-dots{position:absolute;left:563px;top:641px;display:flex;gap:8px}
.hero-dots span{width:18px;height:18px;border-radius:50%;border:2px solid var(--white)}
.hero-dots span:first-child{background:var(--white)}

/* welcome */
.welcome{position:absolute;left:0;top:723px;width:1200px;height:580px}
.welcome-text{position:absolute;left:0;top:0;width:588px;height:580px;background:var(--orange);color:var(--white)}
.welcome-text h2{position:absolute;left:109px;top:104px;font-weight:700;font-size:28px;line-height:38px}
.welcome-text h2 b{display:block;font-size:37px;line-height:44px}
.welcome-text p{position:absolute;left:109px;top:230px;width:400px;font-size:15px;line-height:24px}
.welcome-more{left:109px;top:426px;width:146px;height:40px}
.welcome-photo{position:absolute;left:588px;top:0;width:612px;height:580px;background:linear-gradient(180deg,#5e666d 0%,#8d959a 40%,#c9ccce 70%,#9ea2a4 100%)}

/* section titles */
.section-title{position:absolute;left:0;width:1200px;text-align:center;color:var(--ink);font-weight:700;font-size:38px;text-transform:uppercase}
.section-title::after{content:"";position:absolute;left:565px;width:70px;height:4px;background:var(--orange)}
.services-title{top:1392px}
.services-title::after{top:62px}
.customers-title{top:3580px}
.customers-title::after{top:62px}

/* service cards */
.card{position:absolute;width:440px;background:var(--white);box-shadow:0 2px 8px rgba(0,0,0,.12)}
.card-photo{height:277px}
.card h3{margin:36px 0 0 22px;font-size:18px;font-weight:700;color:var(--ink);text-transform:uppercase;letter-spacing:.3px}
.card ul{list-style:none;margin:18px 0 0 22px}
.card li{position:relative;padding-left:24px;font-size:13.5px;line-height:28.7px;color:var(--muted)}
.card li::before{content:"›";position:absolute;left:0;top:7px;width:13px;height:13px;border:1.5px solid var(--orange);border-radius:50%;color:var(--orange);font-size:13px;line-height:10px;text-align:center;font-weight:700}
.card .btn{position:absolute;left:22px;width:128px;height:36px;font-size:13px}
.card-accent{border-left:3px solid var(--orange)}
.card-1{left:135px;top:1528px;height:606px}
.card-2{left:623px;top:1528px;height:606px}
.card-3{left:135px;top:2183px;height:582px}
.card-4{left:623px;top:2183px;height:582px}
.card-1 .btn,.card-2 .btn{top:537px}
.card-3 .btn,.card-4 .btn{top:515px}
.photo-insulation{background:linear-gradient(180deg,#5a4a3c,#cfcac0 55%,#8c8578)}
.photo-roof{background:linear-gradient(180deg,#3c74c8 0%,#9dbde6 40%,#d6cf96 60%,#c7b551 100%)}
.photo-restoration{background:linear-gradient(180deg,#355f9e 0%,#8fb3dc 35%,#b9c0c9 60%,#5e6a7a 100%)}
.photo-coating{background:linear-gradient(180deg,#6a7f8a 0%,#cfe0ea 45%,#9fb9cf 100%)}

/* video */
.video{position:absolute;left:135px;top:2829px;width:928px;height:481px;background:linear-gradient(90deg,#2d2ea3 0%,#3a3bc4 35%,#9a9ca8 60%,#6e7a5e 100%)}
.video-play{position:absolute;left:433px;top:210px}
.features{position:absolute;left:135px;top:3310px;width:928px;height:170px;display:flex}
.feature{flex:1;background:var(--dark);color:var(--white);display:flex;flex-direction:column;align-items:center;justify-content:flex-start;padding-top:38px;text-align:center;font-weight:700;font-size:14px;line-height:23px;text-transform:uppercase}
.feature svg{margin-bottom:18px}
.feature-highlight{background:var(--orange)}

/* testimonial */
.quote{position:absolute;left:0;top:3690px;width:1200px;text-align:center;font-size:16px;line-height:30px;color:var(--text)}
.quote-mark{position:absolute;font-size:80px;font-weight:900;color:#cfcfcf;line-height:1}
.quote-author{position:absolute;left:0;top:3829px;width:1200px;text-align:center;font-size:14.5px;line-height:27px;color:var(--text)}
.slider-arrow{position:absolute}

/* partners */
.partners{position:absolute;left:143px;top:3980px;display:flex;gap:15px}
.partner{width:171px;height:98px;border:1px solid var(--line);display:flex;align-items:center;justify-content:center;background:var(--white)}
.partner span{display:block;width:80px;height:56px;border-radius:50%;background:#d7d7d7}
.partner .wide{width:120px;height:30px;border-radius:4px}

/* quote form */
.free-quote{position:absolute;left:0;top:4184px;width:1200px;height:488px;background:linear-gradient(90deg,#e9a11a,#f0a81c 50%,#eea51a)}
.free-quote h2{position:absolute;left:145px;top:116px;color:var(--white);font-weight:700;font-size:36px;line-height:43px;text-transform:uppercase}
.free-quote p{position:absolute;left:145px;top:248px;width:330px;font-size:15px;line-height:24px;color:var(--white)}
.field{position:absolute;background:var(--white);border:1px solid #e6e6e6;font-size:12px;color:#555;padding:12px 16px}
.submit{left:539px;top:324px;width:151px;height:40px;background:var(--ink);color:var(--white);font-size:15px;border-radius:2px}

/* footer */
.site-footer{position:absolute;left:0;top:4672px;width:1200px;height:362px;background:var(--dark);color:#cfcfcf;font-size:14px}
.footer-brand{position:absolute;left:141px;top:88px;display:flex;align-items:center;gap:10px}
.footer-brand .brand-mark{width:60px;height:60px}
.socials{position:absolute;left:145px;top:168px;display:flex;gap:12px}
.socials span{width:29px;height:29px;border:1.5px solid #cfcfcf;border-radius:50%}
.copyright{position:absolute;left:141px;top:226px;font-size:13px;line-height:24px}
.footer-col{position:absolute;top:75px}
.footer-col h4{color:var(--white);font-size:17px;font-weight:700;text-transform:uppercase;margin-bottom:26px}
.footer-col li{list-style:none;line-height:27px;font-size:13.5px}
.contact-item{position:relative;padding-left:32px;line-height:18px;margin-bottom:14px;font-size:13.5px}
.contact-item svg{position:absolute;left:0;top:2px}
</style>
</head>
<body>

<section class="hero">
  <div class="abs" role="img" aria-label="Crew member spraying foam on an industrial roof" style="left:0;top:0;width:1200px;height:723px"></div>
  <h1 class="hero-title">Spray Foam<br>Roofing Applications</h1>
  <div class="btn btn-dark hero-phone">1-555-214-0187</div>
  <div class="btn btn-orange hero-quote">Request a free quote</div>
  <div class="hero-dots"><span></span><span></span><span></span></div>
</section>

<header class="site-header">
  <div class="brand"><span class="brand-mark"></span><span class="brand-name">Harbor Seal Works</span></div>
  <nav class="main-nav"><span class="active">HOME</span><span>ABOUT US</span><span>OUR SERVICES</span><span>PROJECTS</span><span>CONTACT US</span></nav>
  <div class="header-cta">FREE QUOTE</div>
</header>

<section class="welcome">
  <div class="welcome-text">
    <h2>Welcome to<b>Harbor Seal Works</b></h2>
    <p>Sed ut perspiciatis unde omnis iste natus sit voluptatem accusantium doloremque laudantium, totam rem aperiam, eaque ipsa quae ab illo inventore veritatis et quasi architecto beatae vitae dicta sunt explicabo. Nemo enim ipsam voluptatem quia voluptas sit aspernatur aut odit aut fugit, sed quia consequuntur magni dolores eos</p>
    <div class="btn btn-dark welcome-more">Learn more</div>
  </div>
  <div class="welcome-photo" role="img" aria-label="Freshly coated white metal roof at an industrial plant"></div>
</section>

<h2 class="section-title services-title">Our Services</h2>

<article class="card card-1 card-accent">
  <div class="card-photo photo-insulation" role="img" aria-label="Warehouse interior with sprayed foam wall insulation"></div>
  <h3>Interior Foam Insulation</h3>
  <ul>
    <li>Improve energy efficiency - up to 45% energy savings</li>
    <li>Maintain consistent temperatures</li>
    <li>Increase racking strength</li>
    <li>Firm adherence to framing members and substrates</li>
    <li>Reduce HAVC size</li>
    <li>FEMA- approved , flood - resistant insulation material</li>
  </ul>
  <div class="btn btn-orange">Learn more</div>
</article>

<article class="card card-2">
  <div class="card-photo photo-roof" role="img" aria-label="Flat commercial roof with fresh yellow spray foam"></div>
  <h3>Foam Roof Application</h3>
  <ul>
    <li>Lifetime maintainable system</li>
    <li>seamless self - adhering system</li>
    <li>weather durability</li>
    <li>Energy conservation</li>
    <li>zero thermal bridging</li>
    <li>Fire retardant</li>
  </ul>
  <div class="btn btn-orange">Learn more</div>
</article>

<article class="card card-3">
  <div class="card-photo photo-restoration" role="img" aria-label="Restored ribbed metal roof under blue sky"></div>
  <h3>Roof Restoration</h3>
  <ul>
    <li>Repair without replacing - eliminates tear off</li>
    <li>warranties available</li>
    <li>Preserve, protect , and prolong roof life</li>
    <li>UV light resistant - cooler roof - cooler interior</li>
    <li>Energy savings</li>
  </ul>
  <div class="btn btn-orange">Learn more</div>
</article>

<article class="card card-4">
  <div class="card-photo photo-coating" role="img" aria-label="Roller applying white coating to a metal roof"></div>
  <h3>Coating Systems</h3>
  <ul>
    <li>Repair without replacing - eliminates tear off</li>
    <li>warranties available</li>
    <li>Preserve, protect , and prolong roof life</li>
    <li>UV light resistant - cooler roof - cooler interior</li>
    <li>Energy savings</li>
  </ul>
  <div class="btn btn-orange">Learn more</div>
</article>

<div class="video" role="img" aria-label="Video still of a blue spray foam insulation rig trailer with open side door">
  <svg class="video-play" width="62" height="62" viewBox="0 0 62 62"><circle cx="31" cy="31" r="29" fill="rgba(255,255,255,.35)" stroke="#fff" stroke-width="2"/><path d="M25 19 L44 31 L25 43 Z" fill="#fff"/></svg>
</div>
<div class="features">
  <div class="feature">
    <svg width="44" height="40" viewBox="0 0 44 40"><path d="M4 4 H20 L40 24 L26 38 L4 16 Z" fill="#fff"/><circle cx="12" cy="12" r="3.5" fill="#232323"/></svg>
    Save up to 45%<br>on your energy bills
  </div>
  <div class="feature feature-highlight">
    <svg width="40" height="36" viewBox="0 0 40 36"><path d="M20 2 L38 18 H33 V34 H24 V24 H16 V34 H7 V18 H2 Z" fill="#fff"/></svg>
    New home or upgrade<br>existing insulation
  </div>
  <div class="feature">
    <svg width="40" height="38" viewBox="0 0 40 38"><path d="M10 2 H30 V14 A10 10 0 0 1 10 14 Z" fill="#fff"/><path d="M10 5 H3 V9 A7 7 0 0 0 10 16 M30 5 H37 V9 A7 7 0 0 1 30 16" fill="none" stroke="#fff" stroke-width="3"/><rect x="17" y="23" width="6" height="7" fill="#fff"/><rect x="11" y="30" width="18" height="6" fill="#fff"/></svg>
    Highest level of<br>performance
  </div>
</div>

<h2 class="section-title customers-title">Our Happy Customers</h2>
<span class="quote-mark" style="left:275px;top:3680px">“</span>
<p class="quote">Sed ut perspiciatis unde omnis iste natus error sit voluptatem accusantium<br>doloremque laudantium, totam rem aperiam, eaque ipsa quae ab illo inventore<br>veritatis et quasi architecto beatae vitae dicta sunt explicabo. Nemo enim ipsam<br>voluptatem quia voluptas sit aspernatur aut odit aut fugit</p>
<div class="quote-author">Daniel Corwin<br>Harbor Seal Works,</div>
<span class="quote-mark" style="left:740px;top:3840px">”</span>
<svg class="slider-arrow" style="left:140px;top:3744px" width="22" height="34" viewBox="0 0 22 34"><path d="M18 2 L4 17 L18 32" fill="none" stroke="#777" stroke-width="3"/></svg>
<svg class="slider-arrow" style="left:1034px;top:3744px" width="22" height="34" viewBox="0 0 22 34"><path d="M4 2 L18 17 L4 32" fill="none" stroke="#777" stroke-width="3"/></svg>

<svg class="slider-arrow" style="left:90px;top:4016px" width="16" height="28" viewBox="0 0 16 28"><path d="M13 2 L3 14 L13 26" fill="none" stroke="#bbb" stroke-width="2"/></svg>
<div class="partners">
  <div class="partner"><span></span></div>
  <div class="partner"><span style="width:64px;height:64px"></span></div>
  <div class="partner"><span style="width:72px;height:72px"></span></div>
  <div class="partner"><span class="wide"></span></div>
  <div class="partner"><span class="wide"></span></div>
</div>
<svg class="slider-arrow" style="left:1094px;top:4016px" width="16" height="28" viewBox="0 0 16 28"><path d="M3 2 L13 14 L3 26" fill="none" stroke="#bbb" stroke-width="2"/></svg>

<section class="free-quote">
  <h2>Get your free<br>quote</h2>
  <p>Sed ut perspiciatis unde omnis iste natus sit voluptatem accusantium doloremque laudantium, totam rem aperiam, eaque ipsa quae ab illo inventore veritatis et quasi architecto beatae vitae dicta</p>
  <div class="field" style="left:539px;top:111px;width:250px;height:39px">First name</div>
  <div class="field" style="left:804px;top:111px;width:251px;height:39px">Last Name</div>
  <div class="field" style="left:539px;top:160px;width:250px;height:39px">Email</div>
  <div class="field" style="left:804px;top:160px;width:251px;height:39px">Phone Number</div>
  <div class="field" style="left:539px;top:209px;width:516px;height:96px">Message</div>
  <div class="btn submit">Submit</div>
</section>

<footer class="site-footer">
  <div class="footer-brand"><span class="brand-mark"></span><span class="brand-name">Harbor Seal Works</span></div>
  <div class="socials"><span></span><span></span><span></span></div>
  <p class="copyright">(c) 2020 Harbor Seal Works, LLC.<br>All Rights Reserved</p>

  <div class="footer-col" style="left:430px">
    <h4>Contact Us</h4>
    <div class="contact-item"><svg width="16" height="20" viewBox="0 0 16 20"><path d="M8 19 C3 12 1 9 1 7 A7 7 0 0 1 15 7 C15 9 13 12 8 19 Z" fill="none" stroke="#cfcfcf" stroke-width="1.5"/><circle cx="8" cy="7" r="2.5" fill="none" stroke="#cfcfcf" stroke-width="1.5"/></svg>Harbor Seal Works, LLC<br>412 Tidewater Ln.<br>Port Alder, CA 90000</div>
    <div class="contact-item"><svg width="16" height="18" viewBox="0 0 16 18"><path d="M3 1 L6 1 L7 5 L5 7 C6 10 8 12 11 13 L13 11 L15 12 L15 15 C15 16 14 17 13 17 C6 16 1 11 1 3 C1 2 2 1 3 1 Z" fill="none" stroke="#cfcfcf" stroke-width="1.5"/></svg>Phone:<br>1-555-214-0187</div>
    <div class="contact-item"><svg width="18" height="14" viewBox="0 0 18 14"><rect x="1" y="1" width="16" height="12" fill="none" stroke="#cfcfcf" stroke-width="1.5"/><path d="M1 1 L9 8 L17 1" fill="none" stroke="#cfcfcf" stroke-width="1.5"/></svg>E-mail:<br>info@harborsealworks.example</div>
  </div>
  <div class="footer-col" style="left:723px">
    <h4>Quick Links</h4>
    <ul><li>Home</li><li>About Us</li><li>Our Services</li><li>Projects</li><li>Contact Us</li></ul>
  </div>
  <div class="footer-col" style="left:899px">
    <h4>Working Hours</h4>
    <ul><li>Mon - Fri: 8am - 8pm</li><li>Saturday: 9am - 7pm</li><li>Sunday: 9am - 8pm</li></ul>
  </div>
</footer>

</body>
</html>
```